Marlowe Group needs a business card

I would like the card to be simple but modern and elegant.
I like black and white.
or black and gold.
we are a private finance lender and also are involved in property and property developments.

please look at the business card photos i provided i would like M.G only one one side and all the other details on the other side use fonts that tie in with my theme.

Industry/Entity Type

Finance

Contact Information for Business Card

Marlowe Group (M.G) Daniel Marlowe M: 0413586207 E: danmarl@inboxmail.test

Font styles to use
Other font styles liked:
• Use fonts that would reflect our business

Colors
000000
ffffff

Requirements
Must have
• one side of details
• other side has either M.G or Marlowe Group like in the photos provided

```html
<!DOCTYPE html>
<html lang="en">
<head>
<meta charset="utf-8">
<title>Marlowe Group – Business Card</title>
<link rel="stylesheet" href="https://fonts.googleapis.com/css2?family=Cinzel:wght@400;700&family=Lato:wght@400&display=swap">
<style>
  :root {
    --backdrop: #6d6d6d;
    --card-white: #ffffff;
    --ink: #111111;
    --card-black: #050508;
    --card-black-edge: #1a1a20;
    --gold: #e2b72c;
    --rule: #bdbdbd;
  }
  html, body {
    margin: 0;
    padding: 0;
    width: 1200px;
    height: 900px;
    overflow: hidden;
    background: var(--backdrop);
  }
  .canvas {
    position: relative;
    width: 1200px;
    height: 900px;
  }
  .card {
    position: absolute;
    top: 271px;
    width: 457px;
    height: 282px;
    border-radius: 16px;
    box-shadow: 2px 4px 6px rgba(0,0,0,0.35);
    overflow: hidden;
  }
  .card--details {
    left: 137px;
    background: var(--card-white);
    color: var(--ink);
  }
  .card--brand {
    left: 626px;
    background:
      radial-gradient(ellipse 30% 55% at 50% 100%, rgba(120,120,130,0.35), transparent 70%),
      linear-gradient(90deg, var(--card-black) 0%, var(--card-black-edge) 50%, var(--card-black) 100%);
  }
  .monogram {
    position: absolute;
    left: 0;
    right: 0;
    text-align: center;
    font-family: "Cinzel", serif;
    font-weight: 400;
    letter-spacing: 2px;
  }
  .card--details .monogram {
    top: 60px;
    font-size: 54px;
    color: var(--ink);
  }
  .card--brand .monogram {
    top: 88px;
    font-size: 58px;
    color: var(--gold);
  }
  .holder-name {
    position: absolute;
    top: 182px;
    left: 0;
    right: 0;
    margin: 0;
    text-align: center;
    font-family: "Cinzel", serif;
    font-weight: 700;
    font-size: 17px;
    letter-spacing: 0.5px;
  }
  .name-rule {
    position: absolute;
    top: 211px;
    left: 163px;
    width: 130px;
    height: 1px;
    background: linear-gradient(90deg, transparent, var(--rule) 35%, var(--rule) 65%, transparent);
  }
  .contact-line {
    position: absolute;
    top: 220px;
    left: 0;
    right: 0;
    text-align: center;
    font-family: "Lato", sans-serif;
    font-size: 13px;
    margin: 0;
  }
  .contact-line .divider { margin: 0 4px 0 8px; }
  .company-name {
    position: absolute;
    top: 193px;
    left: 0;
    right: 0;
    margin: 0;
    text-align: center;
    font-family: "Cinzel", serif;
    font-weight: 400;
    font-size: 20px;
    color: var(--gold);
    letter-spacing: 0.5px;
  }
</style>
</head>
<body>
  <main class="canvas">
    <section class="card card--details">
      <div class="monogram">M.G</div>
      <h1 class="holder-name">Daniel Marlowe</h1>
      <div class="name-rule"></div>
      <p class="contact-line">M: 0413586207 <span class="divider">|</span> E: danmarl@inboxmail.test</p>
    </section>
    <section class="card card--brand">
      <div class="monogram">M.G</div>
      <p class="company-name">Marlowe Group</p>
    </section>
  </main>
</body>
</html>
```